Webdesign für Zahnarztpraxis
Zielgruppe
Zahnarztpraxis
Aufgabenstellung
- Klares und übersichtliches Desgin
- Nicht zu verspielt
- Informativ
- Leichte Naviagtion
- Das Design der alten Webseite soll NICHT kopiert werden
- Die Farben Blau und Grün aus dem Logo sollen sich wiederfinden
- Designbeispiele, die dem Kunden gefallen sind https://www.falkmann-ostrup-zahnarztpraxis.de/ und https://www.zahvilkorn.de/

```html
<!DOCTYPE html>
<html lang="de">
<head>
<meta charset="utf-8">
<title>Praxis Lindenau – Zahnarztpraxis</title>
<link rel="stylesheet" href="https://fonts.googleapis.com/css2?family=Poppins:wght@300;400;500;600&family=Lato:wght@400;700&display=swap">
<style>
:root{
  --blue:#1e98d7;
  --green:#6cb33f;
  --green-soft:#e4f0da;
  --text:#2b2b2b;
  --white:#ffffff;
  --photo-a:#dfe6ea;
  --photo-b:#f4f6f7;
}
*{margin:0;padding:0;box-sizing:border-box}
html,body{width:1200px;height:3724px;overflow:hidden}
body{position:relative;background:var(--white);color:var(--text);font-family:"Lato",sans-serif}
.abs{position:absolute}
.topbar{left:0;top:0;width:1200px;height:48px;background:var(--blue);color:var(--white);font-family:"Poppins",sans-serif;font-size:13px;font-weight:500}
.topbar .item{position:absolute;top:14px;display:flex;align-items:center;gap:10px}
.hero{left:0;top:48px;width:1200px;height:545px}
.brand{left:101px;top:104px;display:flex;align-items:center;gap:12px;font-family:"Poppins",sans-serif;font-weight:500;font-size:30px;color:var(--blue)}
.brand .dot{width:38px;height:38px;border-radius:50%;background:var(--green)}
.nav a{position:absolute;top:84px;font-family:"Poppins",sans-serif;font-size:15px;font-weight:500;color:var(--text);text-decoration:none}
.nav a.active{border-bottom:2px solid var(--green);padding-bottom:3px}
.hero-title{left:100px;top:270px;font-family:"Poppins",sans-serif;font-size:32px;font-weight:300;line-height:44px}
.hero-title strong{font-weight:600;display:block}
.btn{position:absolute;width:195px;height:40px;background:var(--green);color:var(--white);font-family:"Poppins",sans-serif;font-weight:500;font-size:15px;display:flex;align-items:center;justify-content:center;box-shadow:0 2px 4px rgba(0,0,0,.25)}
.notice{left:866px;top:404px;width:300px;color:var(--white);font-size:14px;line-height:18px}
.notice h2{font-family:"Poppins",sans-serif;font-size:24px;font-weight:500;margin-bottom:14px}
.notice p+p{margin-top:18px}
.blob{border-radius:50%;background:var(--green-soft)}
.photo{border-radius:50%;background:radial-gradient(circle at 40% 35%,var(--photo-b),var(--photo-a))}
.block h2{font-family:"Poppins",sans-serif;font-size:24px;font-weight:500;margin-bottom:6px}
.block p{font-family:"Poppins",sans-serif;font-size:14px;font-weight:300;line-height:22px}
.services-title{left:0;width:1200px;top:1250px;text-align:center;font-family:"Poppins",sans-serif;font-size:24px;font-weight:500}
.service{position:absolute;width:170px;margin-left:-85px;text-align:center;font-family:"Poppins",sans-serif;font-size:15px;font-weight:500;line-height:23px}
.service svg{display:block;margin:0 auto 6px}
.footer{left:0;top:3218px;width:1200px;height:506px;background:var(--blue);color:var(--white);font-size:14px;line-height:18px}
.footer .col{position:absolute;top:54px}
.footer h3{font-family:"Poppins",sans-serif;font-size:15px;font-weight:600;margin:30px 0 32px}
.footer p{margin-bottom:18px}
.footer .row{display:flex}
.footer .row span:first-child{width:80px;flex:none}
.footer a{color:var(--white)}
.legal{position:absolute;top:472px;font-family:"Poppins",sans-serif;font-size:15px;font-weight:300}
</style>
</head>
<body>
<svg width="0" height="0" style="position:absolute">
  <defs>
    <symbol id="tooth" viewBox="0 0 80 80">
      <path d="M14 10c-8 6-8 20-3 30 3 7 3 14 4 24 1 7 8 7 9 0l3-16c1-5 5-5 6 0l3 16c1 7 8 7 9 0 1-10 1-17 4-24" fill="none" stroke="#6cb33f" stroke-width="4" stroke-linecap="round"/>
      <path d="M14 10c6-4 12-3 16 0 4 3 8 3 12 0" fill="none" stroke="#6cb33f" stroke-width="4" stroke-linecap="round"/>
      <circle cx="58" cy="22" r="12" fill="#fff" stroke="#6cb33f" stroke-width="4"/>
      <path d="M58 15v14M51 22h14" stroke="#6cb33f" stroke-width="4" stroke-linecap="round"/>
    </symbol>
  </defs>
</svg>

<header class="abs topbar">
  <div class="item" style="left:784px">
    <svg width="22" height="16" viewBox="0 0 22 16"><rect x="1" y="1" width="20" height="14" rx="2" fill="none" stroke="#fff" stroke-width="2"/><path d="M2 2l9 7 9-7" fill="none" stroke="#fff" stroke-width="2"/></svg>
    info@zahnpraxis-lindenau.de
  </div>
  <div class="item" style="left:1062px">
    <svg width="20" height="20" viewBox="0 0 24 24"><path d="M5 3l4 1 1 5-2 2c1 3 3 5 6 6l2-2 5 1 1 4c0 2-2 3-4 2C10 20 4 14 3 7 2 5 3 3 5 3z" fill="none" stroke="#fff" stroke-width="2"/></svg>
    03741 / 58210
  </div>
</header>

<section class="abs hero">
  <svg width="1200" height="545" style="position:absolute;left:0;top:0">
    <defs>
      <linearGradient id="heroBg" x1="0" y1="0" x2="1" y2="1">
        <stop offset="0" stop-color="#eef1f3"/><stop offset="1" stop-color="#dfe4e7"/>
      </linearGradient>
    </defs>
    <rect width="1200" height="545" fill="url(#heroBg)" role="img" aria-label="Behandlungsraum mit Regal und Behandlungsstuhl"/>
    <path d="M0 407 Q420 520 1200 545 L0 545 Z" fill="var(--green)"/>
    <path d="M376 480 C700 400 1000 300 1200 198 L1200 545 L1150 545 Q700 520 376 480 Z" fill="var(--blue)"/>
  </svg>
</section>

<div class="abs brand"><span class="dot"></span>Praxis Lindenau</div>

<nav class="nav">
  <a class="active" href="#" style="left:600px">Unsere Praxis</a>
  <a href="#" style="left:732px">Leistungen</a>
  <a href="#" style="left:838px">Praxislabor</a>
  <a href="#" style="left:956px">Team</a>
  <a href="#" style="left:1035px">Kontakt</a>
</nav>

<h1 class="abs hero-title">Herzlich Willkommen in unserer Praxis!<strong>Ihr Wohlbefinden ist unser Anspruch.</strong></h1>
<a class="btn" style="left:262px;top:390px">Termin vereinbaren</a>

<aside class="abs notice">
  <h2>Praxisschließung</h2>
  <p>in der Zeit von xx.xx.2025 - einschließlich xx.xx.2025 bleibt unsere Praxis geschlossen.</p>
  <p>Die Vertretung in dieser Zeit übernimmt Frau/Herr ... Bitte melden Sie sich im Vorfeld telefonisch an.</p>
</aside>

<div class="abs blob" style="left:954px;top:810px;width:548px;height:548px"></div>
<div class="abs photo" style="left:84px;top:680px;width:468px;height:468px" role="img" aria-label="Heller Behandlungsraum mit Zahnarztstuhl und Monitor"></div>
<div class="abs block" style="left:671px;top:804px;width:420px">
  <h2>Unsere Praxis</h2>
  <p>Praxis &amp; Dentallabor in Talheim.</p>
  <p style="margin-top:38px;font-family:'Lato',sans-serif;font-weight:400;line-height:18px">Prävention und Individualprophylaxe in jeder Altersgruppe!<br>Zahnärztin spricht auch fließend Englisch.</p>
</div>
<a class="btn" style="left:671px;top:970px">Mehr erfahren</a>

<h2 class="abs services-title">Unsere Leistungen</h2>
<div class="service" style="left:182px;top:1326px"><svg width="76" height="76"><use href="#tooth"/></svg>Zahnärztliche<br>Diagnostik</div>
<div class="service" style="left:353px;top:1324px"><svg width="76" height="76"><use href="#tooth"/></svg>Individual-<br>prophylaxe</div>
<div class="service" style="left:518px;top:1324px"><svg width="76" height="76"><use href="#tooth"/></svg>Professionelle<br>Zahnreinigung</div>
<div class="service" style="left:687px;top:1324px"><svg width="76" height="76"><use href="#tooth"/></svg>Konservierende<br>Zahnheilkunde</div>
<div class="service" style="left:857px;top:1324px"><svg width="76" height="76"><use href="#tooth"/></svg>Zahnärztliche<br>Prothetik</div>
<div class="service" style="left:1026px;top:1324px"><svg width="76" height="76"><use href="#tooth"/></svg>Kieferorthopädie</div>
<div class="service" style="left:262px;top:1506px"><svg width="76" height="76"><use href="#tooth"/></svg>Chirurgische<br>Zahnheilkunde</div>
<div class="service" style="left:432px;top:1506px"><svg width="76" height="76"><use href="#tooth"/></svg>Ästhetische<br>Zahnheilkunde</div>
<div class="service" style="left:597px;top:1506px"><svg width="76" height="76"><use href="#tooth"/></svg>Ganzheitliche<br>Zahnheilkunde</div>
<div class="service" style="left:766px;top:1506px"><svg width="76" height="76"><use href="#tooth"/></svg>Kinderzahn-<br>heilkunde</div>
<div class="service" style="left:937px;top:1506px"><svg width="76" height="76"><use href="#tooth"/></svg>Bioverträglicher<br>Zahnersatz</div>
<a class="btn" style="left:528px;top:1683px">Mehr erfahren</a>

<div class="abs blob" style="left:-86px;top:1948px;width:650px;height:650px"></div>
<div class="abs photo" style="left:484px;top:1817px;width:662px;height:608px;background:radial-gradient(ellipse at 50% 40%,#f5f7f4,#c9d8b8)" role="img" aria-label="Praxisteam in weißer Kleidung im Grünen"></div>
<div class="abs block" style="left:136px;top:2186px;width:360px">
  <h2>Unser Praxisteam</h2>
  <p>kompetent, herzlich und darauf fokussiert, Ihre Zahngesundheit bestmöglich zu unterstützen.</p>
</div>
<a class="btn" style="left:136px;top:2351px">Mehr erfahren</a>

<div class="abs blob" style="left:190px;top:2568px;width:440px;height:440px"></div>
<div class="abs photo" style="left:126px;top:2569px;width:544px;height:544px;background:radial-gradient(circle at 55% 40%,#f2ece6,#d9c9c0)" role="img" aria-label="Wartezimmer mit Blumenarrangement"></div>
<div class="abs block" style="left:733px;top:2764px;width:420px">
  <h2>Unser Praxislabor</h2>
  <p>Unsere Praxis verfügt über ein eigenes Praxislabor.</p>
</div>
<a class="btn" style="left:733px;top:2867px">Mehr erfahren</a>

<footer class="abs footer">
  <div class="col" style="left:100px;width:300px">
    <svg width="24" height="30" viewBox="0 0 24 30"><path d="M12 1C6 1 1 6 1 12c0 8 11 17 11 17s11-9 11-17C23 6 18 1 12 1z" fill="#fff"/><circle cx="12" cy="12" r="4" fill="var(--blue)"/></svg>
    <h3>So erreichen Sie uns</h3>
    <p>Birkenweg 14<br>08523 Talheim</p>
    <p>Telefon: 03741-58210<br>Fax: 03741-58219</p>
    <p>E-Mail: info@zahnpraxis-lindenau.de</p>
  </div>
  <div class="col" style="left:467px;width:290px">
    <svg width="28" height="28" viewBox="0 0 28 28"><circle cx="14" cy="14" r="12" fill="none" stroke="#fff" stroke-width="2.5"/><path d="M14 7v7l5 3" fill="none" stroke="#fff" stroke-width="2.5" stroke-linecap="round"/></svg>
    <h3>Unsere Öffnungszeiten</h3>
    <p>
      <span class="row"><span>Montag:</span><span>9:00 bis 13:00 Uhr und<br>14:00 bis 19:00 Uhr</span></span>
      <span class="row"><span>Dienstag:</span><span>9:00 bis 13:00 Uhr und<br>14:00 bis 19:00 Uhr</span></span>
      <span class="row">Mittwoch:&nbsp; 9:00 bis 14:00 Uhr</span>
      <span class="row">Donnerstag: geschlossen</span>
      <span class="row"><span>Freitag:</span><span>9:00 bis 13:00 Uhr</span></span>
    </p>
    <p>... und nach Vereinbarung</p>
    <p>Infomieren Sie sich bitte hier über Aktualisierungen auf unserem Praxis-Eintrag bei Suchportal.</p>
  </div>
  <div class="col" style="left:823px;width:290px">
    <svg width="30" height="28" viewBox="0 0 30 28"><path d="M5 3l4 1 1 5-2 2c1 3 3 5 6 6l2-2 5 1 1 4c0 2-2 3-4 2C10 20 4 14 3 7 2 5 3 3 5 3z" fill="none" stroke="#fff" stroke-width="2"/><path d="M17 3a8 8 0 0 1 8 8M17 7a4 4 0 0 1 4 4" fill="none" stroke="#fff" stroke-width="2"/></svg>
    <h3>Telefonzeiten</h3>
    <p>Innerhalb dieser Zeiten sind wir für Sie telefonisch erreichbar:</p>
    <p>
      <span class="row"><span>Montag:</span><span>9:00 bis 15:00 Uhr</span></span>
      <span class="row"><span>Dienstag:</span><span>9:00 bis 15:00 Uhr</span></span>
      <span class="row"><span>Mittwoch:</span><span>9:00 bis 12:00 Uhr</span></span>
    </p>
    <p>In dringenden Fällen wenden Sie sich bitte an zahnärtlichen Notdienst.</p>
    <p>Link 'zur Notdienstsuche' <a href="#">https://www.zahnnotdienst-region.de/patienten/notdienstsuche/</a></p>
  </div>
  <span class="legal" style="left:471px">Impressum</span>
  <span class="legal" style="left:580px">Datenschutz</span>
  <span class="legal" style="left:698px">AGB</span>
</footer>
</body>
</html>
```